Marine Services Letterhead design

We need a letterhead design for an Australian owned company in Victoria named K+T Harbour Works Pty Ltd. We provide linesmen and launches to assist the large ships that come into port.
Our colour is orange.
The final design should have a strong nautical theme and communicate safety and reliability.
I would like to use the letter head on invoices so it should print to pdf well.

Target Market(s)

Owners and representatives of shipping companies. It is not for general public

Industry/Entity Type

Nautical

Requirements
Must have
• A shipping theme, not overly complicated, featuring safety orange colours but not all orange of course.
The letterhead should just sit at the top of the page so I can use for invoices.
Nice to have
• Something elegant and stylish
Should not have
• cartoons or pop art

```html
<!DOCTYPE html>
<html lang="en">
<head>
<meta charset="utf-8">
<title>K+T Harbour Works Pty Ltd — Letterhead</title>
<link rel="stylesheet" href="https://fonts.googleapis.com/css2?family=Open+Sans:wght@400;600;700&display=swap">
<style>
  :root {
    --paper: #ffffff;
    --ink: #1a1a1a;
    --muted-ink: #3b3b3b;
    --rust: #b0672a;
    --rule: #8a8a8a;
    --footer-text: #ffffff;
  }
  html, body {
    margin: 0;
    padding: 0;
    width: 961px;
    height: 1200px;
    overflow: hidden;
    background: var(--paper);
  }
  .letterhead {
    position: relative;
    width: 961px;
    height: 1200px;
    background: var(--paper);
    font-family: "Open Sans", sans-serif;
    color: var(--ink);
  }
  .brand {
    position: absolute;
    left: 43px;
    top: 62px;
    display: flex;
    align-items: center;
    gap: 16px;
  }
  .brand-mark {
    width: 56px;
    height: 56px;
    background: var(--rust);
  }
  .brand-name {
    font-weight: 700;
    font-size: 22px;
    letter-spacing: -0.2px;
    color: var(--ink);
  }
  .contact {
    position: absolute;
    left: 762px;
    top: 103px;
    padding-left: 9px;
    border-left: 1.5px solid var(--rule);
    font-size: 16.5px;
    line-height: 34px;
    color: var(--muted-ink);
  }
  .contact-line {
    display: flex;
    align-items: center;
    gap: 3px;
    white-space: nowrap;
  }
  .contact-line svg { width: 16px; height: 16px; }
  .footer-wave {
    position: absolute;
    left: 0;
    top: 0;
    width: 961px;
    height: 1200px;
  }
  .footer-address {
    position: absolute;
    left: 0;
    right: 0;
    top: 1166px;
    display: flex;
    justify-content: center;
    align-items: center;
    gap: 5px;
    color: var(--footer-text);
    font-size: 18px;
    letter-spacing: 1.6px;
  }
  .footer-address svg { width: 12px; height: 18px; }
</style>
</head>
<body>
<main class="letterhead">
  <header class="brand">
    <div class="brand-mark"></div>
    <div class="brand-name">K+T Harbour Works Pty Ltd</div>
  </header>

  <address class="contact" style="font-style:normal">
    <div class="contact-line">
      <svg viewBox="0 0 16 16" aria-hidden="true"><circle cx="8" cy="8" r="6.5" fill="none" stroke="var(--rust)" stroke-width="1.3"/><path d="M6 4.5 C4.5 6.5 5.5 10 8.5 11.5 L9.5 10.3 L8.3 9.2 L7.6 9.8 C6.9 9 6.6 8 6.9 7 L7.8 6.6 L7.3 5 Z" fill="var(--rust)"/></svg>
      <span>1300 418 276</span>
    </div>
    <div class="contact-line"><span>ABN: 48203661795</span></div>
  </address>

  <svg class="footer-wave" viewBox="0 0 961 1200" aria-hidden="true">
    <path d="M0,1074 C120,1128 260,1146 430,1138 C610,1128 800,1124 961,1146 L961,1149 C800,1131 610,1136 430,1146 C260,1156 100,1148 0,1118 Z" fill="var(--ink)"/>
    <path d="M0,1124 C110,1150 260,1158 430,1150 C610,1140 800,1134 961,1151 L961,1200 L0,1200 Z" fill="var(--rust)"/>
  </svg>

  <footer class="footer-address">
    <svg viewBox="0 0 12 18" aria-hidden="true"><path d="M6 0 C2.7 0 0 2.6 0 5.8 C0 10 6 18 6 18 C6 18 12 10 12 5.8 C12 2.6 9.3 0 6 0 Z M6 8.2 A2.4 2.4 0 1 1 6 3.4 A2.4 2.4 0 1 1 6 8.2 Z" fill="var(--footer-text)"/></svg>
    <span>PO Box 214 Seaview 3931</span>
  </footer>
</main>
</body>
</html>
```